Business Card for a New Zealand IT Startup

I need a business card for VELTA Holdings. We are a young startup based in New Zealand working in internet marketing and web development. The design should have some element connected to New Zealand, such as wave, koru or silver fern, just don't use a kiwi bird.

```html
<!DOCTYPE html>
<html lang="en">
<head>
<meta charset="utf-8">
<title>VELTA Holdings – Business Card</title>
<link href="https://fonts.googleapis.com/css2?family=Jost:wght@400;500;600&display=swap" rel="stylesheet">
<style>
  :root {
    --blue: #1f74c2;
    --orange: #f05a24;
    --ink: #3a3a3a;
    --rule: #b9b9b9;
    --paper: #ffffff;
    --backdrop: #ece8e2;
    --wave-light: rgba(255,255,255,0.16);
  }
  * { margin: 0; padding: 0; box-sizing: border-box; }
  html, body { width: 1200px; height: 1040px; overflow: hidden; }
  body {
    background: var(--backdrop);
    font-family: "Jost", "Helvetica Neue", Arial, sans-serif;
    position: relative;
  }
  .card {
    position: absolute;
    left: 250px;
    width: 700px;
    height: 400px;
    overflow: hidden;
    box-shadow: 0 6px 18px rgba(0,0,0,0.18);
  }
  .card-front { top: 90px; background: var(--paper); }
  .card-back { top: 550px; background: var(--orange); }

  /* front */
  .brand {
    position: absolute;
    right: 70px;
    top: 62px;
    display: flex;
    align-items: center;
    gap: 12px;
    white-space: nowrap;
    color: var(--blue);
    font-weight: 600;
    font-size: 36px;
    letter-spacing: 3px;
    line-height: 1;
  }
  .brand-dot {
    width: 20px; height: 20px; border-radius: 50%;
    background: var(--blue); flex: none;
  }
  .person { position: absolute; left: 44px; top: 166px; }
  .person-name {
    color: var(--blue); font-size: 34px; font-weight: 400; line-height: 1;
    letter-spacing: -0.5px; white-space: nowrap;
  }
  .person-title {
    color: var(--orange); font-size: 20px; font-weight: 400; margin-top: 4px;
  }
  .divider {
    position: absolute; left: 44px; right: 70px; top: 234px;
    height: 1px; background: var(--rule);
  }
  .contacts {
    position: absolute; left: 44px; top: 246px;
    list-style: none; color: var(--ink); font-size: 18px; line-height: 24px;
  }
  .contacts li { display: flex; align-items: center; gap: 10px; white-space: nowrap; }
  .contacts svg { width: 15px; height: 15px; fill: var(--blue); flex: none; }
  .address {
    position: absolute; right: 70px; top: 246px;
    text-align: right; color: var(--ink); font-size: 18px; line-height: 24px;
    white-space: nowrap;
  }
  .band { position: absolute; left: 0; bottom: 0; width: 700px; height: 80px; }
  .website {
    position: absolute; right: 36px; bottom: 20px;
    color: #fff; font-size: 17px; letter-spacing: 0.3px; white-space: nowrap;
  }

  /* back */
  .back-waves { position: absolute; left: 0; bottom: 0; width: 700px; height: 160px; }
  .back-brand {
    position: absolute; left: 0; right: 0; top: 120px;
    display: flex; justify-content: center; align-items: center; gap: 16px;
    white-space: nowrap;
    color: #fff; font-weight: 600; font-size: 52px; letter-spacing: 4px; line-height: 1;
  }
  .back-brand .brand-dot { background: #fff; width: 26px; height: 26px; }
  .back-url {
    position: absolute; left: 0; right: 0; top: 196px;
    text-align: center; color: #fff; font-size: 18px; letter-spacing: 5px;
  }
</style>
</head>
<body>
  <section class="card card-front" aria-label="Business card front">
    <div class="brand"><span class="brand-dot"></span>VELTA HOLDINGS</div>

    <div class="person">
      <div class="person-name">LIAM CARTER</div>
      <div class="person-title">CEO/FOUNDER</div>
    </div>

    <div class="divider"></div>

    <ul class="contacts">
      <li><svg viewBox="0 0 16 16"><path d="M3 1l3 3-1.5 2a9 9 0 0 0 5.5 5.5L12 10l3 3-2 2C7 15 1 9 1 3z"/></svg>021 555 0142</li>
      <li><svg viewBox="0 0 16 16"><path d="M4 0h8v16H4zM5.5 2v10h5V2z"/></svg>021 555 0187</li>
      <li><svg viewBox="0 0 16 16"><path d="M2 5h12v8H2zM4 1h8v3H4zM4 10h8v4H4z"/></svg>04 555 0163</li>
      <li><svg viewBox="0 0 16 16"><path d="M1 3h14v10H1zM2 4l6 5 6-5"/></svg>liam@veltaholdings.com</li>
    </ul>

    <div class="address">42 Harbour Street<br>Wellington, New Zealand 6011</div>

    <svg class="band" viewBox="0 0 700 80" preserveAspectRatio="none" aria-hidden="true">
      <path d="M0 44 C80 36 160 52 240 44 S360 36 400 44 L410 62 H0 Z" fill="var(--orange)"/>
      <path d="M0 62 H400 Q412 62 418 48 L424 26 Q430 10 450 10 H700 V80 H0 Z" fill="var(--blue)"/>
    </svg>
    <div class="website">www.veltaholdings.com</div>
  </section>

  <section class="card card-back" aria-label="Business card back">
    <svg class="back-waves" viewBox="0 0 700 160" preserveAspectRatio="none" aria-hidden="true">
      <path d="M0 70 C120 30 230 110 350 70 S580 30 700 70 V160 H0 Z" fill="var(--wave-light)"/>
      <path d="M0 110 C120 75 230 145 350 110 S580 75 700 110 V160 H0 Z" fill="var(--wave-light)"/>
    </svg>
    <div class="back-brand"><span class="brand-dot"></span>VELTA HOLDINGS</div>
    <div class="back-url">veltaholdings.com</div>
  </section>
</body>
</html>
```